Nivel Crest - Powerpoint Templates

We are a consultancy to help builders to optimize their planning in order to save building costs. For that reason we need templates for teasers and presentations where we offer our services, show our team and their capacities and present workflows, organization charts, price lists etc.

```html
<!DOCTYPE html>
<html lang="en">
<head>
<meta charset="utf-8">
<title>Nivel Crest – Presentation Template</title>
<link href="https://fonts.googleapis.com/css2?family=Montserrat:wght@400;500;600;700&family=Oswald:wght@600;700&family=Open+Sans:wght@400;600&display=swap" rel="stylesheet">
<style>
:root{
  --bg:#d8d8d8;
  --paper:#ffffff;
  --gold:#c8952f;
  --gold-light:#f1cd70;
  --gold-deep:#a8741f;
  --charcoal:#3b3b3e;
  --charcoal-deep:#2a2a2c;
  --ink:#1b1b1b;
  --text:#3a3a3a;
  --grey:#9c9ca0;
  --gold-grad:linear-gradient(100deg,#b07b25 0%,#d9a947 40%,#f1cd70 62%,#c08a2c 100%);
}
*{box-sizing:border-box;margin:0;padding:0}
html,body{width:1104px;height:1200px;overflow:hidden;background:var(--bg)}
body{position:relative;font-family:"Open Sans",sans-serif;color:var(--text)}
.slide{position:absolute;width:260px;height:163px;background:var(--paper);overflow:hidden}
.abs{position:absolute}
.copy{font-size:3.1px;line-height:1.45;color:var(--text);text-align:justify}
.copy p+p{margin-top:3px}
.brand{position:absolute;display:flex;align-items:center;gap:2px;font-family:"Montserrat",sans-serif;font-weight:700;font-size:4.2px;letter-spacing:.3px;color:#fff}
.brand i{display:block;width:5px;height:5px;background:currentColor}
.brand.lg{font-size:8px;gap:4px;color:var(--gold)}
.brand.lg i{width:10px;height:10px}
.hbar{position:absolute;top:0;right:0;width:170px;height:20px;background:var(--gold-grad);clip-path:polygon(12px 0,100% 0,100% 100%,0 100%)}
.hbar .brand{right:10px;top:7px}
.heading{position:absolute;left:10px;top:6px;font-family:"Montserrat",sans-serif;font-size:7.4px;color:var(--ink)}
.heading b{font-weight:500;color:var(--gold)}
.foot{position:absolute;left:0;bottom:8px;width:222px;height:1.4px;background:var(--gold-grad)}
.foot-label{position:absolute;right:9px;bottom:6.5px;font-family:"Montserrat",sans-serif;font-size:2.8px;color:var(--text)}
.dtitle{font-family:"Montserrat",sans-serif;font-weight:600;font-size:12px;line-height:1;color:var(--ink)}
.dtitle span{display:block;color:var(--gold)}
.item-title{font-family:"Montserrat",sans-serif;font-size:4.4px;font-weight:500;color:var(--ink);margin-bottom:1px}
.gold-title{font-family:"Montserrat",sans-serif;font-size:5.2px;font-weight:500;color:var(--gold);margin-bottom:2px}
.dot{position:absolute;border-radius:50%;background:var(--gold-grad);display:flex;align-items:center;justify-content:center}
.dot.dark{background:radial-gradient(circle at 35% 30%,#6a6a6e,#1e1e20)}
.dot svg{width:55%;height:55%}
.hex{position:absolute;clip-path:polygon(25% 0,75% 0,100% 50%,75% 100%,25% 100%,0 50%);display:flex;align-items:center;justify-content:center}
.photo{position:absolute}
ul.bul{list-style:none}
ul.bul li{position:relative;padding-left:4px;margin-bottom:4px}
ul.bul li::before{content:"";position:absolute;left:0;top:1.3px;width:1.3px;height:1.3px;background:currentColor}
.center{text-align:center}
.info-note{position:absolute;width:36px;font-size:3.1px;line-height:1.45;color:var(--text)}
</style>
</head>
<body>

<!-- 1 Cover -->
<section class="slide" style="left:111px;top:104px">
  <div class="abs" style="inset:0;background:var(--gold-grad);clip-path:polygon(171px 0,181px 0,141px 163px,131px 163px)"></div>
  <div class="photo" role="img" aria-label="Hazy golden city skyline" style="inset:0;background:linear-gradient(160deg,#cdb25a,#8d7436 55%,#4e4228);clip-path:polygon(181px 0,260px 0,260px 163px,141px 163px)"></div>
  <div class="photo" role="img" aria-label="Modern towers beside a river under blue sky" style="left:117px;top:35px;width:80px;height:80px;border-radius:50%;border:3px solid #fff;box-shadow:0 0 0 2px #2a2a2c;background:linear-gradient(180deg,#2a79c8,#8cc6ec 45%,#5d8a64 75%,#2f5a7a)"></div>
  <div class="brand lg" style="left:12px;top:12px"><i></i>NIVEL CREST</div>
  <div class="abs" style="left:11px;top:100px;font-family:'Oswald',sans-serif;font-weight:700;font-size:19px;line-height:1;color:var(--ink)">PRESENTATION</div>
  <div class="abs" style="left:11px;top:120px;font-family:'Oswald',sans-serif;font-weight:700;font-size:19px;line-height:1;color:var(--gold)">TITLE GOESHERE</div>
  <div class="abs" style="left:11px;top:144px;font-family:'Montserrat',sans-serif;font-size:5.4px;color:var(--ink)">Subtitle of Presentation Goes Here</div>
</section>

<!-- 2 About -->
<section class="slide" style="left:421px;top:104px">
  <div class="abs dtitle" style="left:18px;top:26px">ABOUT<span>COMPANY</span></div>
  <div class="abs" style="inset:0;background:var(--gold-grad);clip-path:polygon(143px 0,260px 0,260px 49px,119px 49px)"></div>
  <div class="abs copy" style="left:140px;top:17px;width:112px;color:#fff">Lorem ipsum dolor sit amet, consectetuer adipiscing elit, sed diam nonummy nibh euismod tincidunt ut laoreet dolore magna aliquam erat volutpat. Ut wisi enim ad minim veniam, quis nostrud exerci tation ullamcorper suscipit lobortis nisl ut aliquip ex ea commodo consequat.</div>
  <div class="abs copy" style="left:18px;top:63px;width:108px"><p>Lorem ipsum dolor sit amet, consectetuer adipiscing elit, sed diam nonummy nibh euismod tincidunt ut laoreet dolore magna aliquam erat volutpat. Ut wisi enim ad minim veniam, quis nostrud exerci tation ullamcorper suscipit lobortis nisl ut aliquip ex ea commodo consequat.</p><p>Lorem ipsum dolor sit amet, consectetuer adipiscing elit, sed diam nonummy nibh euismod tincidunt ut laoreet dolore magna aliquam erat volutpat. Ut wisi enim ad minim veniam, quis nostrud exerci tation ullamcorper suscipit lobortis nisl ut aliquip ex ea commodo consequat. Duis autem vel eum iriure dolor in hendrerit in vulputate velit esse molestie consequat, vel illum dolore eu feugiat nulla.</p></div>
  <div class="abs copy" style="left:137px;top:63px;width:108px"><p>Lorem ipsum dolor sit amet, consectetuer adipiscing elit, sed diam nonummy nibh euismod tincidunt ut laoreet dolore magna aliquam erat volutpat. Ut wisi enim ad minim veniam, quis nostrud exerci tation ullamcorper suscipit lobortis nisl ut aliquip ex ea commodo consequat.</p><p>Lorem ipsum dolor sit amet, consectetuer adipiscing elit, sed diam nonummy nibh euismod tincidunt ut laoreet dolore magna aliquam erat volutpat. Ut wisi enim ad minim veniam, quis nostrud exerci tation ullamcorper suscipit lobortis nisl ut aliquip ex ea commodo consequat. Duis autem vel eum iriure dolor in hendrerit in vulputate velit esse molestie consequat, vel illum dolore eu feugiat nulla.</p></div>
  <div class="foot"></div><div class="foot-label">NIVEL CREST | 01</div>
</section>

<!-- 3 Mission -->
<section class="slide" style="left:732px;top:104px">
  <div class="abs dtitle" style="left:12px;top:26px">OUR MISSION<span>OUR VISION</span></div>
  <div class="abs copy" style="left:12px;top:57px;width:110px"><p>Lorem ipsum dolor sit amet, consectetuer adipiscing elit, sed diam nonummy nibh euismod tincidunt ut laoreet dolore magna aliquam erat volutpat. Ut wisi enim ad minim veniam, quis nostrud exerci tation ullamcorper suscipit lobortis nisl ut aliquip ex ea commodo consequat. Duis autem vel eum iriure dolor in hendrerit.</p><p style="margin-top:8px">Lorem ipsum dolor sit amet, consectetuer adipiscing elit, sed diam nonummy nibh euismod tincidunt ut laoreet dolore magna aliquam erat volutpat. Ut wisi enim ad minim veniam, quis nostrud exerci tation ullamcorper suscipit lobortis nisl ut aliquip ex ea commodo consequat. Duis autem vel eum iriure dolor in hendrerit in vulputate velit esse molestie consequat, vel illum dolore eu feugiat nulla facilisis at vero eros.</p></div>
  <div class="abs" style="left:142px;top:32px;width:118px;height:39px;background:var(--gold-grad)"></div>
  <div class="abs" style="left:142px;top:92px;width:118px;height:39px;background:linear-gradient(100deg,#2a2a2c,#5a5a5e 60%,#2f2f31)"></div>
  <div class="hex" style="left:128px;top:37px;width:30px;height:27px;background:var(--charcoal)"><svg viewBox="0 0 20 20" width="11" height="11"><circle cx="10" cy="8" r="5" fill="none" stroke="#fff" stroke-width="1.6"/><rect x="8" y="13" width="4" height="3" fill="#fff"/></svg></div>
  <div class="hex" style="left:128px;top:97px;width:30px;height:27px;background:var(--gold-grad)"><svg viewBox="0 0 20 20" width="12" height="12"><path d="M2 11l5-4 3 2 3-2 5 4-6 4z" fill="#fff"/></svg></div>
  <div class="abs" style="left:162px;top:37px;width:92px"><div class="item-title" style="color:#fff">Title Goes Here</div><div class="copy" style="color:#fff">Lorem ipsum dolor sit amet, consectetuer adipiscing elit, sed diam nonummy nibh euismod tincidunt ut laoreet dolore magna aliquam erat volutpat. Ut wisi enim ad minim veniam, quis nostrud exerci tation.</div></div>
  <div class="abs" style="left:162px;top:97px;width:92px"><div class="item-title" style="color:#fff">Title Goes Here</div><div class="copy" style="color:#fff">Lorem ipsum dolor sit amet, consectetuer adipiscing elit, sed diam nonummy nibh euismod tincidunt ut laoreet dolore magna aliquam erat volutpat. Ut wisi enim ad minim veniam, quis nostrud exerci tation.</div></div>
  <div class="foot"></div><div class="foot-label">NIVEL CREST | 01</div>
</section>

<!-- 4 Services text -->
<section class="slide" style="left:111px;top:315px">
  <div class="heading"><b>Heading</b> Goes Here</div>
  <div class="hbar"><div class="brand"><i></i>NIVEL CREST</div></div>
  <div class="abs" style="left:10px;top:27px;width:240px">
    <div class="gold-title" style="font-weight:400">Service Title Goes Here</div>
    <div class="copy"><p>Lorem ipsum dolor sit amet, consectetuer adipiscing elit, sed diam nonummy nibh euismod tincidunt ut laoreet dolore magna aliquam erat volutpat. Ut wisi enim ad minim veniam, quis nostrud exerci tation ullamcorper suscipit lobortis nisl ut aliquip ex ea commodo consequat. Duis autem vel eum iriure dolor in hendrerit in vulputate velit esse molestie consequat, vel illum dolore eu feugiat nulla facilisis at vero eros et accumsan et iusto odio dignissim qui blandit praesent luptatum zzril.</p><p>Lorem ipsum dolor sit amet, consectetuer adipiscing elit, sed diam nonummy nibh euismod tincidunt ut laoreet dolore magna aliquam erat volutpat. Ut wisi enim ad minim veniam, quis nostrud exerci tation ullamcorper suscipit lobortis nisl ut aliquip ex ea commodo consequat. Duis autem vel eum iriure dolor in hendrerit in vulputate velit esse molestie consequat, vel illum dolore eu feugiat nulla facilisis at vero eros et accumsan et iusto odio dignissim qui blandit praesent luptatum zzril delenit augue duis dolore te feugait nulla facilisi.</p></div>
    <div class="gold-title" style="font-weight:400;margin-top:4px">Service Title Goes Here</div>
    <div class="copy"><p>Lorem ipsum dolor sit amet, consectetuer adipiscing elit, sed diam nonummy nibh euismod tincidunt ut laoreet dolore magna aliquam erat volutpat. Ut wisi enim ad minim veniam, quis nostrud exerci tation ullamcorper suscipit lobortis nisl ut aliquip ex ea commodo consequat. Duis autem vel eum iriure dolor in hendrerit in vulputate velit esse molestie consequat, vel illum dolore eu feugiat nulla facilisis at vero eros et accumsan et iusto odio dignissim qui blandit praesent luptatum zzril delenit augue duis dolore te feugait nulla facilisi.</p></div>
  </div>
  <div class="foot"></div><div class="foot-label">NIVEL CREST | 01</div>
</section>

<!-- 5 List with photo -->
<section class="slide" style="left:421px;top:315px">
  <div class="heading"><b>Heading</b> Goes Here</div>
  <div class="photo" role="img" aria-label="Dark city skyline at dusk" style="inset:0;background:linear-gradient(200deg,#6e6e72,#3a3a3e 45%,#1c1c1e);clip-path:polygon(174px 0,260px 0,260px 163px,132px 163px)"></div>
  <div class="brand" style="right:10px;top:8px"><i></i>NIVEL CREST</div>
  <div class="dot dark" style="left:10px;top:47px;width:18px;height:18px"><svg viewBox="0 0 20 20"><circle cx="10" cy="6" r="3.5" fill="#fff"/><path d="M3 18c0-5 3-7 7-7s7 2 7 7z" fill="#fff"/></svg></div>
  <div class="dot" style="left:10px;top:79px;width:18px;height:18px"><svg viewBox="0 0 20 20"><circle cx="10" cy="6" r="3.5" fill="#fff"/><path d="M3 18c0-5 3-7 7-7s7 2 7 7z" fill="#fff"/></svg></div>
  <div class="dot dark" style="left:10px;top:112px;width:18px;height:18px"><svg viewBox="0 0 20 20"><circle cx="10" cy="6" r="3.5" fill="#fff"/><path d="M3 18c0-5 3-7 7-7s7 2 7 7z" fill="#fff"/></svg></div>
  <div class="abs" style="left:36px;top:45px;width:88px"><div class="item-title">Title Goes Here</div><div class="copy">Lorem ipsum dolor sit amet, consectetuer adipiscing elit, sed diam nonummy nibh euismod tincidunt ut laoreet dolore magna aliquam erat volutpat. Ut wisi enim ad minim veniam.</div></div>
  <div class="abs" style="left:36px;top:77px;width:88px"><div class="item-title">Title Goes Here</div><div class="copy">Lorem ipsum dolor sit amet, consectetuer adipiscing elit, sed diam nonummy nibh euismod tincidunt ut laoreet dolore magna aliquam erat volutpat. Ut wisi enim ad minim veniam.</div></div>
  <div class="abs" style="left:36px;top:110px;width:88px"><div class="item-title">Title Goes Here</div><div class="copy">Lorem ipsum dolor sit amet, consectetuer adipiscing elit, sed diam nonummy nibh euismod tincidunt ut laoreet dolore magna aliquam erat volutpat. Ut wisi enim ad minim veniam.</div></div>
  <div class="foot-label" style="color:#fff">NIVEL CREST | 01</div>
</section>

<!-- 6 Gold diagonal with hex list -->
<section class="slide" style="left:732px;top:315px">
  <div class="abs" style="inset:0;background:var(--gold-grad);clip-path:polygon(0 0,172px 0,85px 163px,0 163px)"></div>
  <div class="abs" style="left:10px;top:8px;font-family:'Montserrat',sans-serif;font-size:11px;line-height:1.1;color:#fff">Heading<br>Goes Here</div>
  <div class="brand" style="right:10px;top:8px;color:var(--gold)"><i></i>NIVEL CREST</div>
  <div class="abs copy" style="left:12px;top:52px;width:96px;color:#fff"><p>Lorem ipsum dolor sit amet, consectetuer adipiscing elit, sed diam nonummy nibh euismod tincidunt ut laoreet dolore magna aliquam erat volutpat. Ut wisi enim ad minim veniam, quis nostrud exerci tation ullamcorper suscipit lobortis nisl ut aliquip ex ea commodo consequat.</p><p style="margin-top:5px">Lorem ipsum dolor sit amet, consectetuer adipiscing elit, sed diam nonummy nibh euismod tincidunt ut laoreet dolore magna aliquam erat volutpat. Ut wisi enim ad minim veniam, quis nostrud exerci tation ullamcorper suscipit lobortis nisl ut aliquip ex ea commodo consequat.</p></div>
  <div class="hex" style="left:140px;top:26px;width:26px;height:23px;background:#fff"><div class="hex" style="position:static;width:21px;height:18px;background:var(--gold)"><svg viewBox="0 0 20 20" width="9" height="9"><circle cx="10" cy="8" r="5" fill="none" stroke="#fff" stroke-width="1.8"/><rect x="8" y="13" width="4" height="3" fill="#fff"/></svg></div></div>
  <div class="hex" style="left:123px;top:57px;width:26px;height:23px;background:#fff"><div class="hex" style="position:static;width:21px;height:18px;background:var(--gold)"><svg viewBox="0 0 20 20" width="9" height="9"><circle cx="10" cy="8" r="5" fill="none" stroke="#fff" stroke-width="1.8"/><rect x="8" y="13" width="4" height="3" fill="#fff"/></svg></div></div>
  <div class="hex" style="left:107px;top:89px;width:26px;height:23px;background:#fff"><div class="hex" style="position:static;width:21px;height:18px;background:var(--gold)"><svg viewBox="0 0 20 20" width="9" height="9"><circle cx="10" cy="8" r="5" fill="none" stroke="#fff" stroke-width="1.8"/><rect x="8" y="13" width="4" height="3" fill="#fff"/></svg></div></div>
  <div class="hex" style="left:92px;top:119px;width:26px;height:23px;background:#fff"><div class="hex" style="position:static;width:21px;height:18px;background:var(--gold)"><svg viewBox="0 0 20 20" width="9" height="9"><circle cx="10" cy="8" r="5" fill="none" stroke="#fff" stroke-width="1.8"/><rect x="8" y="13" width="4" height="3" fill="#fff"/></svg></div></div>
  <div class="abs" style="left:168px;top:26px;width:88px"><div class="gold-title" style="font-size:4.6px;margin-bottom:0">Title Goes Here</div><div class="copy">Lorem ipsum dolor sit amet, consectetuer adipiscing elit, sed diam nonummy nibh euismod tincidunt ut laoreet dolore.</div></div>
  <div class="abs" style="left:151px;top:57px;width:100px"><div class="gold-title" style="font-size:4.6px;margin-bottom:0">Title Goes Here</div><div class="copy">Lorem ipsum dolor sit amet, consectetuer adipiscing elit, sed diam nonummy nibh euismod tincidunt ut laoreet dolore.</div></div>
  <div class="abs" style="left:135px;top:89px;width:100px"><div class="gold-title" style="font-size:4.6px;margin-bottom:0">Title Goes Here</div><div class="copy">Lorem ipsum dolor sit amet, consectetuer adipiscing elit, sed diam nonummy nibh euismod tincidunt ut laoreet dolore.</div></div>
  <div class="abs" style="left:120px;top:119px;width:100px"><div class="gold-title" style="font-size:4.6px;margin-bottom:0">Title Goes Here</div><div class="copy">Lorem ipsum dolor sit amet, consectetuer adipiscing elit, sed diam nonummy nibh euismod tincidunt ut laoreet dolore.</div></div>
  <div class="foot" style="left:auto;right:0;width:150px"></div><div class="foot-label">NIVEL CREST | 01</div>
</section>

<!-- 7 Six features -->
<section class="slide" style="left:111px;top:517px">
  <div class="heading"><b>Heading</b> Goes Here</div>
  <div class="hbar"><div class="brand"><i></i>NIVEL CREST</div></div>
  <div class="dot" style="left:10px;top:43px;width:18px;height:18px"><svg viewBox="0 0 20 20"><circle cx="10" cy="6" r="3.5" fill="#fff"/><path d="M3 18c0-5 3-7 7-7s7 2 7 7z" fill="#fff"/></svg></div>
  <div class="dot" style="left:10px;top:75px;width:18px;height:18px"><svg viewBox="0 0 20 20"><circle cx="10" cy="6" r="3.5" fill="#fff"/><path d="M3 18c0-5 3-7 7-7s7 2 7 7z" fill="#fff"/></svg></div>
  <div class="dot" style="left:10px;top:107px;width:18px;height:18px"><svg viewBox="0 0 20 20"><circle cx="10" cy="6" r="3.5" fill="#fff"/><path d="M3 18c0-5 3-7 7-7s7 2 7 7z" fill="#fff"/></svg></div>
  <div class="dot" style="left:135px;top:43px;width:18px;height:18px"><svg viewBox="0 0 20 20"><circle cx="10" cy="6" r="3.5" fill="#fff"/><path d="M3 18c0-5 3-7 7-7s7 2 7 7z" fill="#fff"/></svg></div>
  <div class="dot" style="left:135px;top:75px;width:18px;height:18px"><svg viewBox="0 0 20 20"><circle cx="10" cy="6" r="3.5" fill="#fff"/><path d="M3 18c0-5 3-7 7-7s7 2 7 7z" fill="#fff"/></svg></div>
  <div class="dot" style="left:135px;top:107px;width:18px;height:18px"><svg viewBox="0 0 20 20"><circle cx="10" cy="6" r="3.5" fill="#fff"/><path d="M3 18c0-5 3-7 7-7s7 2 7 7z" fill="#fff"/></svg></div>
  <div class="abs" style="left:32px;top:40px;width:1px;height:90px;background:#ccc"></div>
  <div class="abs" style="left:157px;top:40px;width:1px;height:90px;background:#ccc"></div>
  <div class="abs" style="left:37px;top:41px;width:90px"><div class="item-title">Title Goes Here</div><div class="copy" style="font-size:3.6px;text-align:left">Lorem ipsum dolor sit amet, consectetuer adipiscing elit, sed diam nonummy nibh euismod tincidunt ut laoreet dolore magna</div></div>
  <div class="abs" style="left:37px;top:73px;width:90px"><div class="item-title">Title Goes Here</div><div class="copy" style="font-size:3.6px;text-align:left">Lorem ipsum dolor sit amet, consectetuer adipiscing elit, sed diam nonummy nibh euismod tincidunt ut laoreet dolore magna</div></div>
  <div class="abs" style="left:37px;top:105px;width:90px"><div class="item-title">Title Goes Here</div><div class="copy" style="font-size:3.6px;text-align:left">Lorem ipsum dolor sit amet, consectetuer adipiscing elit, sed diam nonummy nibh euismod tincidunt ut laoreet dolore magna</div></div>
  <div class="abs" style="left:162px;top:41px;width:90px"><div class="item-title">Title Goes Here</div><div class="copy" style="font-size:3.6px;text-align:left">Lorem ipsum dolor sit amet, consectetuer adipiscing elit, sed diam nonummy nibh euismod tincidunt ut laoreet dolore magna</div></div>
  <div class="abs" style="left:162px;top:73px;width:90px"><div class="item-title">Title Goes Here</div><div class="copy" style="font-size:3.6px;text-align:left">Lorem ipsum dolor sit amet, consectetuer adipiscing elit, sed diam nonummy nibh euismod tincidunt ut laoreet dolore magna</div></div>
  <div class="abs" style="left:162px;top:105px;width:90px"><div class="item-title">Title Goes Here</div><div class="copy" style="font-size:3.6px;text-align:left">Lorem ipsum dolor sit amet, consectetuer adipiscing elit, sed diam nonummy nibh euismod tincidunt ut laoreet dolore magna</div></div>
  <div class="foot"></div><div class="foot-label">NIVEL CREST | 01</div>
</section>

<!-- 8 Team -->
<section class="slide" style="left:421px;top:517px">
  <div class="abs" style="left:0;top:0;width:260px;height:82px;background:var(--gold-grad)"></div>
  <div class="abs center" style="left:0;top:20px;width:260px;font-family:'Montserrat',sans-serif;font-weight:500;font-size:11.5px;color:#fff">OUR CREATIVE TEAM</div>
  <div class="abs copy center" style="left:35px;top:36px;width:190px;color:#fff">Lorem ipsum dolor sit amet, consectetuer adipiscing elit, sed diam nonummy nibh euismod tincidunt ut laoreet dolore magna aliquam erat volutpat. Ut wisi enim ad minim veniam, quis nostrud exerci tation ullamcorper suscipit lobortis nisl ut aliquip ex ea commodo consequat.</div>
  <div class="dot" style="left:19px;top:55px;width:52px;height:52px;box-shadow:0 0 0 2.5px #fff"><svg viewBox="0 0 20 20" style="width:30%;height:30%"><circle cx="10" cy="6" r="4" fill="#fff"/><path d="M2 19c0-6 3.5-8 8-8s8 2 8 8z" fill="#fff"/></svg></div>
  <div class="dot" style="left:76px;top:55px;width:52px;height:52px;box-shadow:0 0 0 2.5px #fff"><svg viewBox="0 0 20 20" style="width:30%;height:30%"><circle cx="10" cy="6" r="4" fill="#fff"/><path d="M2 19c0-6 3.5-8 8-8s8 2 8 8z" fill="#fff"/></svg></div>
  <div class="dot" style="left:133px;top:55px;width:52px;height:52px;box-shadow:0 0 0 2.5px #fff"><svg viewBox="0 0 20 20" style="width:30%;height:30%"><circle cx="10" cy="6" r="4" fill="#fff"/><path d="M2 19c0-6 3.5-8 8-8s8 2 8 8z" fill="#fff"/></svg></div>
  <div class="dot" style="left:190px;top:55px;width:52px;height:52px;box-shadow:0 0 0 2.5px #fff"><svg viewBox="0 0 20 20" style="width:30%;height:30%"><circle cx="10" cy="6" r="4" fill="#fff"/><path d="M2 19c0-6 3.5-8 8-8s8 2 8 8z" fill="#fff"/></svg></div>
  <div class="abs center" style="left:18px;top:113px;width:54px"><div class="item-title">Name Here</div><div class="copy center">Lorem ipsum dolor sit amet, consectetuer adipiscing elit, sed diam nonummy nibh euismod tincidunt ut laoreet dolore magna aliquam erat volutpat. Ut wisi enim ad minim veniam.</div></div>
  <div class="abs center" style="left:75px;top:113px;width:54px"><div class="item-title">Name Here</div><div class="copy center">Lorem ipsum dolor sit amet, consectetuer adipiscing elit, sed diam nonummy nibh euismod tincidunt ut laoreet dolore magna aliquam erat volutpat. Ut wisi enim ad minim veniam.</div></div>
  <div class="abs center" style="left:132px;top:113px;width:54px"><div class="item-title">Name Here</div><div class="copy center">Lorem ipsum dolor sit amet, consectetuer adipiscing elit, sed diam nonummy nibh euismod tincidunt ut laoreet dolore magna aliquam erat volutpat. Ut wisi enim ad minim veniam.</div></div>
  <div class="abs center" style="left:189px;top:113px;width:54px"><div class="item-title">Name Here</div><div class="copy center">Lorem ipsum dolor sit amet, consectetuer adipiscing elit, sed diam nonummy nibh euismod tincidunt ut laoreet dolore magna aliquam erat volutpat. Ut wisi enim ad minim veniam.</div></div>
  <div class="foot"></div><div class="foot-label">NIVEL CREST | 01</div>
</section>

<!-- 9 Price table -->
<section class="slide" style="left:732px;top:517px">
  <div class="heading"><b>Heading</b> Goes Here</div>
  <div class="hbar"><div class="brand"><i></i>NIVEL CREST</div></div>
  <div class="abs" style="left:10px;top:44px;width:240px;height:12px;background:var(--grey)"></div>
  <div class="abs" style="left:84px;top:42px;width:42px;height:93px;border:1px solid var(--gold);border-radius:2px"></div>
  <div class="abs" style="left:85px;top:43px;width:40px;height:13px;background:var(--gold-grad)"></div>
  <table class="abs" style="left:10px;top:44px;width:240px;border-collapse:collapse;font-family:'Montserrat',sans-serif;font-size:3.3px;color:var(--text)">
    <colgroup><col style="width:74px"><col style="width:42px"><col style="width:41px"><col style="width:41px"><col style="width:42px"></colgroup>
    <tr style="height:12px;color:#fff;text-align:center;line-height:1.1"><td style="text-align:left;padding-left:2px">Heading Goes Here</td><td>Heading<br>Goes Here</td><td>Heading<br>Goes Here</td><td>Heading<br>Goes Here</td><td>Heading<br>Goes Here</td></tr>
    <tr style="height:10.8px;border-bottom:.5px solid #ccc;text-align:center"><td style="text-align:left;padding-left:2px">Lorem Ipsum Goes Here</td><td>23</td><td>12</td><td>78</td><td>12</td></tr>
    <tr style="height:10.8px;border-bottom:.5px solid #ccc;text-align:center"><td style="text-align:left;padding-left:2px">Lorem Ipsum Goes Here</td><td>45</td><td>56</td><td>12</td><td>56</td></tr>
    <tr style="height:10.8px;border-bottom:.5px solid #ccc;text-align:center"><td style="text-align:left;padding-left:2px">Lorem Ipsum Goes Here</td><td>78</td><td>76</td><td>34</td><td>76</td></tr>
    <tr style="height:10.8px;border-bottom:.5px solid #ccc;text-align:center"><td style="text-align:left;padding-left:2px">Lorem Ipsum Goes Here</td><td>22</td><td>12</td><td>55</td><td>12</td></tr>
    <tr style="height:10.8px;border-bottom:.5px solid #ccc;text-align:center"><td style="text-align:left;padding-left:2px">Lorem Ipsum Goes Here</td><td>34</td><td>66</td><td>45</td><td>66</td></tr>
    <tr style="height:10.8px;border-bottom:.5px solid #ccc;text-align:center"><td style="text-align:left;padding-left:2px">Lorem Ipsum Goes Here</td><td>67</td><td>47</td><td>78</td><td>47</td></tr>
    <tr style="height:10.8px;border-bottom:.5px solid #ccc;text-align:center"><td style="text-align:left;padding-left:2px">Lorem Ipsum Goes Here</td><td>87</td><td>67</td><td>12</td><td>67</td></tr>
  </table>
  <div class="foot"></div><div class="foot-label">NIVEL CREST | 01</div>
</section>

<!-- 10 Split bullets -->
<section class="slide" style="left:111px;top:712px">
  <div class="abs" style="left:131px;top:0;width:129px;height:163px;background:var(--charcoal)"></div>
  <div class="heading"><b>Heading</b> Goes Here</div>
  <div class="brand" style="right:10px;top:9px"><i></i>NIVEL CREST</div>
  <div class="abs" style="left:10px;top:35px;width:115px"><div class="gold-title" style="font-weight:600;color:var(--gold-deep)">Curabitur Dapibus Dignissim Dui.</div>
    <ul class="bul copy" style="margin-top:5px"><li>Lorem ipsum dolor sit amet, consectetuer adipiscing elit, sed diam nonummy nibh euismod tincidunt ut laoreet dolore magna aliquam erat volutpat. Ut wisi enim ad minim veniam,</li><li style="margin-top:6px">Lorem ipsum dolor sit amet, consectetuer adipiscing elit, sed diam nonummy nibh euismod tincidunt ut laoreet dolore magna aliquam erat volutpat. Ut wisi enim ad minim veniam, quis nostrud exerci tation ullamcorper suscipit lobortis nisl ut aliquip ex ea commodo consequat. Duis autem vel eum iriure dolor in hendrerit in vulputate velit esse molestie consequat.</li><li style="margin-top:6px">Lorem ipsum dolor sit amet, consectetuer adipiscing elit, sed diam nonummy nibh euismod tincidunt ut laoreet dolore magna aliquam erat volutpat. Ut wisi enim ad minim veniam, quis nostrud exerci tation ullamcorper suscipit lobortis nisl ut aliquip ex ea commodo consequat. Duis autem vel eum iriure dolor in hendrerit in vulputate velit esse molestie consequat.</li></ul></div>
  <div class="abs" style="left:137px;top:35px;width:115px"><div class="gold-title" style="color:#fff">Curabitur Dapibus Dignissim Dui.</div>
    <ul class="bul copy" style="margin-top:5px;color:#fff"><li>Lorem ipsum dolor sit amet, consectetuer adipiscing elit, sed diam nonummy nibh euismod tincidunt ut laoreet dolore magna aliquam erat volutpat. Ut wisi enim ad minim veniam,</li><li style="margin-top:6px">Lorem ipsum dolor sit amet, consectetuer adipiscing elit, sed diam nonummy nibh euismod tincidunt ut laoreet dolore magna aliquam erat volutpat. Ut wisi enim ad minim veniam, quis nostrud exerci tation ullamcorper suscipit lobortis nisl ut aliquip ex ea commodo consequat. Duis autem vel eum iriure dolor in hendrerit in vulputate velit esse molestie consequat.</li><li style="margin-top:6px">Lorem ipsum dolor sit amet, consectetuer adipiscing elit, sed diam nonummy nibh euismod tincidunt ut laoreet dolore magna aliquam erat volutpat. Ut wisi enim ad minim veniam, quis nostrud exerci tation ullamcorper suscipit lobortis nisl ut aliquip ex ea commodo consequat. Duis autem vel eum iriure dolor in hendrerit in vulputate velit esse molestie consequat.</li></ul></div>
  <div class="foot-label" style="color:#ccc">NIVEL CREST | 01</div>
</section>

<!-- 11 Cards and bullets -->
<section class="slide" style="left:421px;top:718px">
  <div class="heading"><b>Heading</b> Goes Here</div>
  <div class="hbar"><div class="brand"><i></i>NIVEL CREST</div></div>
  <div class="abs center" style="left:14px;top:46px;width:56px;height:88px;background:linear-gradient(180deg,#b07b25,#e2b655 45%,#b98328);border-bottom:3px solid var(--ink);color:#fff;padding:6px 4px 0">
    <div class="dot dark" style="position:relative;margin:0 auto;width:10px;height:10px"><svg viewBox="0 0 20 20"><circle cx="10" cy="10" r="6" fill="#fff"/></svg></div>
    <div style="font-family:'Montserrat',sans-serif;font-size:6px;margin:4px 0 3px">Heading</div>
    <div class="copy center" style="color:#fff">Lorem ipsum dolor sit amet, consectetuer adipiscing elit, sed diam nonummy nibh euismod tincidunt ut laoreet dolore magna aliquam erat volutpat. Ut wisi enim ad minim veniam, quis nostrud exerci tation</div></div>
  <div class="abs center" style="left:76px;top:46px;width:56px;height:88px;background:linear-gradient(180deg,#b07b25,#e2b655 45%,#b98328);border-bottom:3px solid var(--ink);color:#fff;padding:6px 4px 0">
    <div class="dot dark" style="position:relative;margin:0 auto;width:10px;height:10px"><svg viewBox="0 0 20 20"><circle cx="10" cy="10" r="6" fill="#fff"/></svg></div>
    <div style="font-family:'Montserrat',sans-serif;font-size:6px;margin:4px 0 3px">Heading</div>
    <div class="copy center" style="color:#fff">Lorem ipsum dolor sit amet, consectetuer adipiscing elit, sed diam nonummy nibh euismod tincidunt ut laoreet dolore magna aliquam erat volutpat. Ut wisi enim ad minim veniam, quis nostrud exerci tation</div></div>
  <div class="abs" style="left:140px;top:46px;width:110px"><div class="gold-title" style="font-weight:600;color:var(--gold-deep)">Curabitur Dapibus Dignissim Dui.</div>
    <ul class="bul copy" style="margin-top:5px"><li>Lorem ipsum dolor sit amet, consectetuer adipiscing elit, sed diam nonummy nibh euismod tincidunt ut laoreet dolore magna aliquam erat volutpat. Ut wisi enim ad minim veniam,</li><li style="margin-top:5px">Lorem ipsum dolor sit amet, consectetuer adipiscing elit, sed diam nonummy nibh euismod tincidunt ut laoreet dolore magna aliquam erat volutpat. Ut wisi enim ad minim veniam, quis nostrud exerci tation ullamcorper suscipit lobortis nisl ut aliquip ex ea commodo consequat. Duis autem vel eum iriure dolor in hendrerit.</li><li style="margin-top:5px">Lorem ipsum dolor sit amet, consectetuer adipiscing elit, sed diam nonummy nibh euismod tincidunt ut laoreet dolore magna aliquam erat volutpat. Ut wisi enim ad minim veniam, quis nostrud exerci tation ullamcorper suscipit lobortis nisl ut aliquip ex ea commodo consequat. Duis autem vel eum iriure dolor in hendrerit.</li></ul></div>
  <div class="foot"></div><div class="foot-label">NIVEL CREST | 01</div>
</section>

<!-- 12 Company services -->
<section class="slide" style="left:732px;top:718px">
  <div class="abs" style="inset:0;background:linear-gradient(115deg,#a8741f,#f1cd70 45%,#6b6b6e 70%,#3b3b3e);clip-path:polygon(155px 0,260px 0,260px 163px,65px 163px)"></div>
  <div class="abs" style="inset:0;background:var(--charcoal);clip-path:polygon(155px 0,260px 0,260px 163px,95px 163px,130px 95px)"></div>
  <div class="abs dtitle" style="left:12px;top:21px">OUR COMPANY<span>SERVICES</span></div>
  <div class="brand" style="right:10px;top:8px"><i></i>NIVEL CREST</div>
  <div class="abs" style="left:12px;top:53px;width:78px"><div class="item-title" style="font-size:3.8px">Title Goes Here</div><div class="copy">Lorem ipsum dolor sit amet, consectetuer adipiscing elit, sed diam nonummy nibh euismod tincidunt ut laoreet dolore magna aliquam erat volutpat. Ut wisi enim ad minim veniam, quis nostrud exerci tation ullamcorper suscipit lobortis nisl ut aliquip ex ea commodo consequat.</div>
    <div class="item-title" style="font-size:3.8px;margin-top:4px">Title Goes Here</div><div class="copy">Lorem ipsum dolor sit amet, consectetuer adipiscing elit, sed diam nonummy nibh euismod tincidunt ut laoreet dolore magna aliquam erat volutpat. Ut wisi enim ad minim veniam, quis nostrud exerci tation ullamcorper suscipit lobortis.</div></div>
  <svg class="abs" style="left:160px;top:40px" width="14" height="14" viewBox="0 0 20 20"><circle cx="9" cy="9" r="6" fill="none" stroke="#fff" stroke-width="2"/><path d="M13 13l5 5" stroke="#fff" stroke-width="2.5"/></svg>
  <svg class="abs" style="left:211px;top:40px" width="14" height="14" viewBox="0 0 20 20"><circle cx="10" cy="10" r="8" fill="none" stroke="#fff" stroke-width="1.5"/><ellipse cx="10" cy="10" rx="3.5" ry="8" fill="none" stroke="#fff" stroke-width="1.2"/><path d="M2 10h16" stroke="#fff" stroke-width="1.2"/></svg>
  <svg class="abs" style="left:160px;top:87px" width="14" height="14" viewBox="0 0 20 20"><path d="M10 12V5M10 7c-3 0-5-2-5-4 3 0 5 1 5 4zM10 7c3 0 5-2 5-4-3 0-5 1-5 4z" fill="#fff" stroke="#fff"/><rect x="6" y="12" width="8" height="6" fill="#fff"/></svg>
  <svg class="abs" style="left:211px;top:87px" width="14" height="14" viewBox="0 0 20 20"><path d="M1 9l5-4 4 3 4-3 5 4-7 6z" fill="#fff"/></svg>
  <div class="abs copy center" style="left:148px;top:57px;width:38px;color:#eee">Lorem ipsum dolor sit amet, consectetuer adipiscing elit, sed diam nonummy nibh euismod tincidunt ut laoreet dolore magna aliquam.</div>
  <div class="abs copy center" style="left:199px;top:57px;width:38px;color:#eee">Lorem ipsum dolor sit amet, consectetuer adipiscing elit, sed diam nonummy nibh euismod tincidunt ut laoreet dolore magna aliquam.</div>
  <div class="abs copy center" style="left:148px;top:104px;width:38px;color:#eee">Lorem ipsum dolor sit amet, consectetuer adipiscing elit, sed diam nonummy nibh euismod tincidunt ut laoreet dolore magna aliquam.</div>
  <div class="abs copy center" style="left:199px;top:104px;width:38px;color:#eee">Lorem ipsum dolor sit amet, consectetuer adipiscing elit, sed diam nonummy nibh euismod tincidunt ut laoreet dolore magna aliquam.</div>
  <div class="foot-label" style="color:#ccc">NIVEL CREST | 01</div>
</section>

<!-- 13 Text with photos -->
<section class="slide" style="left:111px;top:920px">
  <div class="heading"><b>Heading</b> Goes Here</div>
  <div class="hbar"><div class="brand"><i></i>NIVEL CREST</div></div>
  <div class="abs copy" style="left:10px;top:37px;width:240px"><p>Larkfield Planning Group is an independent consultancy that supports private builders from the first sketch to the final handover. We review drawings, schedules and tenders early, so that costly changes are found on paper instead of on site. Our aim is simple: clear decisions, steady budgets and buildings that are delivered on time and to the agreed quality.</p><p>Our team combines architects, engineers and cost planners who have worked on homes, offices and public buildings. We compare offers, check contracts and guide every project step with a plain written plan. Each client receives one contact person and regular reports on progress, costs and open questions.</p></div>
  <div class="photo" role="img" aria-label="Team meeting around an office table" style="left:12px;top:78px;width:71px;height:33px;background:linear-gradient(120deg,#4a4a4a,#cfcfcf 50%,#6a6a6a)"></div>
  <div class="photo" role="img" aria-label="Professional using a tablet in blue light" style="left:95px;top:78px;width:71px;height:33px;background:linear-gradient(120deg,#1f4f8a,#9fc7ea 55%,#2a4d7a)"></div>
  <div class="photo" role="img" aria-label="Colleagues reviewing documents at a desk" style="left:178px;top:78px;width:71px;height:33px;background:linear-gradient(120deg,#e6e6ea,#7b8fb0 55%,#c7ccd6)"></div>
  <div class="abs center gold-title" style="left:12px;top:117px;width:71px;font-size:4.6px">Heading Goes Here</div>
  <div class="abs center gold-title" style="left:95px;top:117px;width:71px;font-size:4.6px">Heading Goes Here</div>
  <div class="abs center gold-title" style="left:178px;top:117px;width:71px;font-size:4.6px">Heading Goes Here</div>
  <ul class="abs bul copy" style="left:12px;top:127px;width:60px;text-align:left"><li>Lorem ipsum dolar sit amet, consectetur adipiscing edit. Vivamus eu dui ex.</li></ul>
  <ul class="abs bul copy" style="left:95px;top:127px;width:60px;text-align:left"><li>Lorem ipsum dolar sit amet, consectetur adipiscing edit. Vivamus eu dui ex.</li></ul>
  <ul class="abs bul copy" style="left:178px;top:127px;width:60px;text-align:left"><li>Lorem ipsum dolar sit amet, consectetur adipiscing edit. Vivamus eu dui ex.</li></ul>
  <div class="foot"></div><div class="foot-label">NIVEL CREST | 01</div>
</section>

<!-- 14 Infographic -->
<section class="slide" style="left:421px;top:920px">
  <div class="heading"><b>Heading</b> Goes Here</div>
  <div class="hbar"><div class="brand"><i></i>NIVEL CREST</div></div>
  <div class="abs center" style="left:0;top:35px;width:260px;font-family:'Montserrat',sans-serif;font-weight:600;font-size:11px;color:var(--gold)">INFOGRAPHIC CHART</div>
  <div class="abs copy center" style="left:40px;top:50px;width:180px">Lorem ipsum dolor sit amet, consectetuer adipiscing elit, sed diam nonummy nibh euismod tincidunt ut laoreet dolore magna aliquam erat volutpat. Ut wisi enim ad minim veniam, quis nostrud exerci tation ullamcorper suscipit lobortis nisl ut aliquip.</div>
  <svg class="abs" style="left:94px;top:72px" width="74" height="74" viewBox="0 0 74 74">
    <defs><linearGradient id="ring" x1="0" y1="0" x2="1" y2="1"><stop offset="0" stop-color="#b07b25"/><stop offset=".5" stop-color="#e2b655"/><stop offset="1" stop-color="#a8741f"/></linearGradient><radialGradient id="core" cx=".4" cy=".35"><stop offset="0" stop-color="#8a8a8e"/><stop offset="1" stop-color="#2a2a2c"/></radialGradient></defs>
    <circle cx="37" cy="37" r="30" fill="none" stroke="url(#ring)" stroke-width="12"/>
    <circle cx="37" cy="37" r="22" fill="#fff"/>
    <circle cx="37" cy="37" r="20" fill="url(#core)"/>
    <circle cx="30" cy="32" r="3.2" fill="#fff"/><circle cx="44" cy="32" r="3.2" fill="#fff"/><circle cx="37" cy="30" r="3.8" fill="#fff"/>
    <path d="M24 45c0-5 3-7 6-7s6 2 6 7zM38 45c0-5 3-7 6-7s6 2 6 7z" fill="#fff"/><path d="M29 46c0-6 4-8 8-8s8 2 8 8z" fill="#fff"/>
    <g font-family="Montserrat,sans-serif" font-size="3.4" fill="#fff" text-anchor="middle"><text x="37" y="9">50%</text><text x="37" y="68">50%</text><text x="9" y="38">50%</text><text x="65" y="38">50%</text><text x="17" y="19">50%</text><text x="57" y="19">50%</text><text x="17" y="59">50%</text><text x="57" y="59">50%</text></g>
  </svg>
  <svg class="abs" style="left:40px;top:80px" width="12" height="12" viewBox="0 0 20 20"><path d="M1 9l5-4 4 3 4-3 5 4-7 6z" fill="var(--gold)"/></svg>
  <svg class="abs" style="left:41px;top:103px" width="10" height="10" viewBox="0 0 20 20"><rect x="2" y="3" width="16" height="11" fill="none" stroke="var(--gold)" stroke-width="2"/><path d="M7 18h6" stroke="var(--gold)" stroke-width="2"/></svg>
  <svg class="abs" style="left:41px;top:126px" width="10" height="10" viewBox="0 0 20 20"><path d="M10 12V5M10 7c-3 0-5-2-5-4 3 0 5 1 5 4zM10 7c3 0 5-2 5-4-3 0-5 1-5 4z" fill="var(--gold)" stroke="var(--gold)"/><rect x="6" y="12" width="8" height="6" fill="var(--gold)"/></svg>
  <svg class="abs" style="left:174px;top:80px" width="10" height="10" viewBox="0 0 20 20"><circle cx="10" cy="8" r="6" fill="none" stroke="var(--gold)" stroke-width="2"/><rect x="7.5" y="14" width="5" height="4" fill="var(--gold)"/></svg>
  <svg class="abs" style="left:174px;top:103px" width="10" height="10" viewBox="0 0 20 20"><circle cx="10" cy="10" r="8" fill="var(--gold)"/><path d="M2 10h16M10 2v16" stroke="#fff" stroke-width="1"/></svg>
  <svg class="abs" style="left:174px;top:126px" width="10" height="10" viewBox="0 0 20 20"><circle cx="10" cy="10" r="6" fill="none" stroke="var(--gold)" stroke-width="3" stroke-dasharray="3 2"/><circle cx="10" cy="10" r="2.5" fill="var(--gold)"/></svg>
  <div class="info-note" style="left:55px;top:79px">Lorem ipsum dolor sit amet, consectetur adipiscing elit. Praesent non nibh.</div>
  <div class="info-note" style="left:55px;top:102px">Lorem ipsum dolor sit amet, consectetur adipiscing elit. Praesent non nibh.</div>
  <div class="info-note" style="left:55px;top:125px">Lorem ipsum dolor sit amet, consectetur adipiscing elit. Praesent non nibh.</div>
  <div class="info-note" style="left:187px;top:79px">Lorem ipsum dolor sit amet, consectetur adipiscing elit. Praesent non nibh.</div>
  <div class="info-note" style="left:187px;top:102px">Lorem ipsum dolor sit amet, consectetur adipiscing elit. Praesent non nibh.</div>
  <div class="info-note" style="left:187px;top:125px">Lorem ipsum dolor sit amet, consectetur adipiscing elit. Praesent non nibh.</div>
  <div class="foot"></div><div class="foot-label">NIVEL CREST | 01</div>
</section>

<!-- 15 Thank you -->
<section class="slide" style="left:732px;top:920px;background:var(--gold-grad)">
  <div class="photo" role="img" aria-label="City skyline with skyscrapers under blue sky" style="inset:0;background:linear-gradient(180deg,#6fa3d6,#b9d4ea 45%,#5a6b7e 75%,#2d3440);clip-path:polygon(131px 0,260px 0,260px 163px,186px 163px)"></div>
  <div class="abs" style="inset:0;background:#f1cd70;clip-path:polygon(126px 0,128px 0,183px 163px,181px 163px)"></div>
  <div class="abs" style="inset:0;background:#f1cd70;clip-path:polygon(137px 0,139px 0,194px 163px,192px 163px)"></div>
  <div class="brand lg" style="left:13px;top:13px;color:#fff"><i></i>NIVEL CREST</div>
  <div class="abs" style="left:12px;top:47px;font-family:'Oswald',sans-serif;font-weight:700;font-size:33px;line-height:1;color:var(--ink)">THANK</div>
  <div class="abs" style="left:12px;top:79px;font-family:'Oswald',sans-serif;font-weight:700;font-size:33px;line-height:1;color:var(--ink)">YOU!</div>
  <div class="abs" style="left:13px;top:138px;font-family:'Montserrat',sans-serif;font-weight:600;font-size:8.5px;color:#fff">PRESENTATION</div>
  <div class="abs" style="left:13px;top:148px;font-family:'Montserrat',sans-serif;font-weight:600;font-size:4.6px;color:#fff">TITLE GOESHERE</div>
</section>

</body>
</html>
```